UI/ UX Design for ERP Software

We need a new UX/UI interface for a ERP software for property managers. Our CMMS / ERP solution is made based on responsive design technologies and is coded in PHP.
The overall UX to be similar to Tev Ulna - easy navigation, intuitive menus.

Industry/Entity Type

Property Management

Number of Pages Required

5+ page

Requirements
Must have
• Round dock buttons
Consistent icons across the application
Enough Spacing between buttons/icons/ menu
Consistent Font
Nice to have
• We would like the UX to allow the users to use the application without /minimum training.
Should not have
• we don't want anything that is classic with respect to UX

```html
<!DOCTYPE html>
<html lang="en">
<head>
<meta charset="utf-8">
<title>Domora – Active Dashboard</title>
<link href="https://fonts.googleapis.com/css2?family=Raleway:wght@400;500;600;700&display=swap" rel="stylesheet">
<style>
:root{
  --blue:#0a7cf3;
  --cyan:#06b8f5;
  --header-bg:#edf6fb;
  --tab-bg:#dff2fc;
  --bar-bg:#52637a;
  --ink:#2b3340;
  --muted:#55606e;
  --grid:#d7dbe0;
  --white:#ffffff;
  --green:#8fe27c;
  --charcoal:#44444c;
  --violet:#8585e0;
  --pink:#ef5b83;
  --yellow:#e3d14a;
  --orange:#f5a04f;
}
*{box-sizing:border-box;margin:0;padding:0}
html,body{width:1200px;height:689px;overflow:hidden;background:var(--white);font-family:"Raleway",sans-serif;color:var(--ink)}
.app{position:relative;width:1200px;height:689px}
.topbar{position:absolute;left:0;top:0;width:1200px;height:59px;background:var(--header-bg)}
.brand{position:absolute;left:20px;top:0;height:59px;display:flex;align-items:center;gap:7px;font-weight:700;font-size:22px;color:var(--blue)}
.brand-mark{width:16px;height:16px;background:var(--blue);border-radius:3px}
.page-tab{position:absolute;left:137px;top:0;width:192px;height:59px;background:var(--tab-bg);display:flex;align-items:center;gap:10px;padding-left:17px;font-size:16px;font-weight:500}
.stat{position:absolute;top:8px;display:flex;align-items:center;height:42px}
.stat-icon{width:42px;height:42px;background:var(--blue);display:flex;align-items:center;justify-content:center}
.stat-text{padding-left:8px;line-height:1.05}
.stat-value{font-weight:700;font-size:15px}
.stat-label{font-size:10px;color:var(--muted);margin-top:3px}
.sidebar{position:absolute;left:0;top:58px;width:51px;height:631px;background:var(--blue)}
.sidebar ul{list-style:none}
.sidebar li{height:27.6px;display:flex;align-items:center;justify-content:center}
.sidebar li:first-child{margin-top:7px}
.range-bar{position:absolute;left:79px;top:78px;width:1087px;height:37px;background:var(--bar-bg)}
.range-tab{position:absolute;top:78px;height:37px;display:flex;align-items:center;gap:4px;color:var(--white);font-size:10px;white-space:nowrap}
.range-tab.active{top:70px;height:46px;left:563px;width:103px;justify-content:center;padding-top:8px;background:linear-gradient(var(--cyan),var(--blue))}
.period{position:absolute;left:83px;top:130px;display:flex;align-items:center;gap:6px;font-size:16px}
.chart{position:absolute;left:80px;top:175px}
.legend{position:absolute;left:138px;top:527px;width:900px;height:90px}
.legend-item{position:absolute;display:flex;align-items:center;gap:7px;font-size:9px;color:var(--muted)}
.swatch{width:18px;height:11px;border-radius:6px}
.page-code{position:absolute;left:1170px;top:663px;font-size:8px;color:var(--muted)}
</style>
</head>
<body>
<div class="app">
  <header class="topbar">
    <div class="brand"><span class="brand-mark"></span>Domora</div>
    <div class="page-tab">
      <svg width="20" height="16" viewBox="0 0 20 16"><path d="M10 1 1 8.5h2.5V15h5v-4h3v4h5V8.5H19z" fill="var(--ink)"/></svg>
      Active Dashboard
    </div>
    <div class="stat" style="left:414px"><div class="stat-icon"><svg width="22" height="18" viewBox="0 0 20 16"><path d="M10 1 1 8.5h2.5V15h5v-4h3v4h5V8.5H19z" fill="#fff"/></svg></div><div class="stat-text"><div class="stat-value">03</div><div class="stat-label">Properties</div></div></div>
    <div class="stat" style="left:525px"><div class="stat-icon"><svg width="24" height="16" viewBox="0 0 24 16" fill="#fff"><circle cx="12" cy="4" r="3.2"/><circle cx="5" cy="5" r="2.4"/><circle cx="19" cy="5" r="2.4"/><path d="M6 15c0-4 3-6 6-6s6 2 6 6zM0 14c0-3 2-5 5-5 1 0 2 .4 2.5 1-1.5 1-2.5 2.5-2.7 4zM24 14c0-3-2-5-5-5-1 0-2 .4-2.5 1 1.5 1 2.5 2.5 2.7 4z"/></svg></div><div class="stat-text"><div class="stat-value">08</div><div class="stat-label">Tenants</div></div></div>
    <div class="stat" style="left:621px"><div class="stat-icon"><svg width="24" height="24" viewBox="0 0 24 24"><path d="M12 1l4 4h-3v6h6V8l4 4-4 4v-3h-6v6h3l-4 4-4-4h3v-6H5v3l-4-4 4-4v3h6V5H8z" fill="#fff"/></svg></div><div class="stat-text"><div class="stat-value">422,000,00.sq.ft</div><div class="stat-label">Total Properties Area</div></div></div>
    <div class="stat" style="left:799px"><div class="stat-icon"><svg width="24" height="24" viewBox="0 0 24 24"><path d="M12 1l4 4h-3v6h6V8l4 4-4 4v-3h-6v6h3l-4 4-4-4h3v-6H5v3l-4-4 4-4v3h6V5H8z" fill="#fff"/></svg></div><div class="stat-text"><div class="stat-value">233,500.00.sq.ft</div><div class="stat-label">Rented Area</div></div></div>
    <div class="stat" style="left:977px"><div class="stat-icon"><svg width="24" height="24" viewBox="0 0 24 24"><path d="M12 1l4 4h-3v6h6V8l4 4-4 4v-3h-6v6h3l-4 4-4-4h3v-6H5v3l-4-4 4-4v3h6V5H8z" fill="#fff"/></svg></div><div class="stat-text"><div class="stat-value">188,500.00sq.ft</div><div class="stat-label">Vacancies Area</div></div></div>
  </header>

  <nav class="sidebar">
    <ul>
      <li><svg width="14" height="12" viewBox="0 0 14 12"><path d="M1 11a6 6 0 1 1 12 0z" fill="#fff"/></svg></li>
      <li><svg width="16" height="11" viewBox="0 0 24 16" fill="#fff"><circle cx="12" cy="4" r="3.2"/><circle cx="5" cy="5" r="2.4"/><circle cx="19" cy="5" r="2.4"/><path d="M6 15c0-4 3-6 6-6s6 2 6 6zM0 14c0-3 2-5 5-5s4 2 4 5zM24 14c0-3-2-5-5-5s-4 2-4 5z"/></svg></li>
      <li><svg width="13" height="13" viewBox="0 0 13 13"><path d="M6.5 1 2 12M6.5 1l4.5 11M2 7h9" stroke="#fff" stroke-width="2" fill="none"/></svg></li>
      <li><svg width="12" height="13" viewBox="0 0 12 13" fill="#fff"><circle cx="6" cy="3.5" r="3"/><path d="M0 13c0-4 3-6 6-6s6 2 6 6z"/></svg></li>
      <li><svg width="16" height="13" viewBox="0 0 16 13"><circle cx="5" cy="7" r="4" fill="none" stroke="#fff" stroke-width="3"/><circle cx="12" cy="4" r="2.5" fill="none" stroke="#fff" stroke-width="2"/><circle cx="12" cy="10.5" r="2" fill="none" stroke="#fff" stroke-width="2"/></svg></li>
      <li><svg width="16" height="11" viewBox="0 0 24 16" fill="#fff"><circle cx="12" cy="4" r="3.2"/><circle cx="5" cy="5" r="2.4"/><circle cx="19" cy="5" r="2.4"/><path d="M6 15c0-4 3-6 6-6s6 2 6 6zM0 14c0-3 2-5 5-5s4 2 4 5zM24 14c0-3-2-5-5-5s-4 2-4 5z"/></svg></li>
      <li><svg width="10" height="13" viewBox="0 0 10 13"><path d="M0 0h6l4 4v9H0z" fill="#fff"/></svg></li>
      <li><svg width="13" height="13" viewBox="0 0 13 13"><path d="M1 1l11 11M12 1 1 12" stroke="#fff" stroke-width="2.5"/></svg></li>
      <li><svg width="12" height="12" viewBox="0 0 12 12"><circle cx="6" cy="6" r="4" fill="none" stroke="#fff" stroke-width="3.5" stroke-dasharray="2.5 1.2"/></svg></li>
      <li><svg width="16" height="12" viewBox="0 0 16 12"><path d="M4 2 0.5 6 4 10M12 2l3.5 4L12 10M9.5 1 6.5 11" stroke="#fff" stroke-width="2" fill="none"/></svg></li>
      <li><svg width="13" height="13" viewBox="0 0 13 13"><circle cx="5" cy="5" r="3.5" fill="none" stroke="#fff" stroke-width="2.2"/><path d="M8 8l4 4" stroke="#fff" stroke-width="2.5"/></svg></li>
      <li><svg width="12" height="12" viewBox="0 0 12 12"><rect width="12" height="12" rx="2" fill="#fff"/><path d="M3.5 9V6M6 9V3M8.5 9V5" stroke="var(--blue)" stroke-width="1.5"/></svg></li>
      <li><svg width="14" height="12" viewBox="0 0 14 12"><path d="M7 0l7 12H0z" fill="#fff"/><path d="M7 4v4" stroke="var(--blue)" stroke-width="1.6"/></svg></li>
      <li><svg width="13" height="12" viewBox="0 0 13 12" fill="#fff"><rect width="13" height="3"/><rect y="4.5" width="13" height="3"/><rect y="9" width="13" height="3"/></svg></li>
      <li><svg width="15" height="10" viewBox="0 0 15 10"><rect width="15" height="10" rx="1" fill="#fff"/><circle cx="7.5" cy="5" r="2.2" fill="var(--blue)"/></svg></li>
      <li><svg width="15" height="12" viewBox="0 0 15 12" fill="#fff"><ellipse cx="6" cy="5" rx="6" ry="4.5"/><ellipse cx="10" cy="7.5" rx="5" ry="4"/></svg></li>
      <li><svg width="10" height="13" viewBox="0 0 10 13"><path d="M0 0h6l4 4v9H0z" fill="#fff"/><path d="M2 7h6M2 9.5h6" stroke="var(--blue)" stroke-width="1.2"/></svg></li>
      <li><svg width="13" height="11" viewBox="0 0 13 11"><path d="M1 0v10h12" stroke="#fff" stroke-width="1.6" fill="none"/><path d="M4 8V4M6.5 8V2M9 8V5M11.5 8V3" stroke="#fff" stroke-width="1.6"/></svg></li>
      <li><svg width="10" height="13" viewBox="0 0 10 13"><path d="M0 0h6l4 4v9H0z" fill="#fff"/></svg></li>
      <li><svg width="10" height="13" viewBox="0 0 10 13"><path d="M0 0h6l4 4v9H0z" fill="#fff"/><path d="M4 1v7" stroke="var(--blue)" stroke-width="1.2" stroke-dasharray="1 1"/></svg></li>
      <li><svg width="16" height="13" viewBox="0 0 16 13"><circle cx="5" cy="7" r="4" fill="none" stroke="#fff" stroke-width="3"/><circle cx="12" cy="4" r="2.5" fill="none" stroke="#fff" stroke-width="2"/><circle cx="12" cy="10.5" r="2" fill="none" stroke="#fff" stroke-width="2"/></svg></li>
      <li><svg width="13" height="13" viewBox="0 0 13 13"><path d="M1 12l6-6" stroke="#fff" stroke-width="2.5"/><circle cx="9" cy="4" r="3" fill="none" stroke="#fff" stroke-width="2"/></svg></li>
    </ul>
  </nav>

  <div class="range-bar"></div>
  <div class="range-tab active"><svg width="12" height="12" viewBox="0 0 12 12"><circle cx="6" cy="6" r="5" fill="none" stroke="#fff" stroke-width="1.4"/><path d="M6 3v3.2l2 1.3" stroke="#fff" stroke-width="1.3" fill="none"/></svg>Last 7 days</div>
  <div class="range-tab" style="left:674px"><svg width="12" height="12" viewBox="0 0 12 12"><circle cx="6" cy="6" r="5" fill="none" stroke="#fff" stroke-width="1.4"/><path d="M6 3v3.2l2 1.3" stroke="#fff" stroke-width="1.3" fill="none"/></svg>Last months</div>
  <div class="range-tab" style="left:766px"><svg width="12" height="12" viewBox="0 0 12 12"><circle cx="6" cy="6" r="5" fill="none" stroke="#fff" stroke-width="1.4"/><path d="M6 3v3.2l2 1.3" stroke="#fff" stroke-width="1.3" fill="none"/></svg>Last 3 months</div>
  <div class="range-tab" style="left:870px"><svg width="12" height="12" viewBox="0 0 12 12"><circle cx="6" cy="6" r="5" fill="none" stroke="#fff" stroke-width="1.4"/><path d="M6 3v3.2l2 1.3" stroke="#fff" stroke-width="1.3" fill="none"/></svg>Next 7 days</div>
  <div class="range-tab" style="left:963px"><svg width="12" height="12" viewBox="0 0 12 12"><circle cx="6" cy="6" r="5" fill="none" stroke="#fff" stroke-width="1.4"/><path d="M6 3v3.2l2 1.3" stroke="#fff" stroke-width="1.3" fill="none"/></svg>Next months</div>
  <div class="range-tab" style="left:1058px"><svg width="12" height="12" viewBox="0 0 12 12"><circle cx="6" cy="6" r="5" fill="none" stroke="#fff" stroke-width="1.4"/><path d="M6 3v3.2l2 1.3" stroke="#fff" stroke-width="1.3" fill="none"/></svg>Next 3 months</div>

  <div class="period">
    <svg width="20" height="20" viewBox="0 0 20 20" fill="var(--bar-bg)"><rect x="0" y="10" width="5" height="10"/><rect x="7" y="3" width="5" height="17"/><rect x="14" y="7" width="5" height="13"/></svg>
    <span>12/27/2020 &nbsp;- &nbsp;01/03/2021</span>
  </div>

  <svg class="chart" width="1090" height="300" viewBox="80 175 1090 300" style="font-family:Raleway, sans-serif">
    <g stroke="var(--muted)" stroke-width="2"><path d="M83 181h15M83 187h15M83 193h15"/></g>
    <g stroke="var(--grid)" stroke-width="1">
      <line x1="149" y1="192.5" x2="1159" y2="192.5"/>
      <line x1="149" y1="246.5" x2="1159" y2="246.5"/>
      <line x1="149" y1="297.5" x2="1159" y2="297.5"/>
      <line x1="149" y1="351.5" x2="1159" y2="351.5"/>
      <line x1="149" y1="404.5" x2="1159" y2="404.5"/>
      <line x1="149" y1="457.5" x2="1159" y2="457.5"/>
    </g>
    <g fill="var(--muted)" style="font-size:11px" text-anchor="end">
      <text x="136" y="194">1.25</text><text x="132" y="247">1</text><text x="132" y="298">0.75</text>
      <text x="132" y="351">0.5</text><text x="132" y="404">0.25</text><text x="132" y="457">0</text>
    </g>
    <text transform="translate(97 340) rotate(-90)" text-anchor="middle" style="font-size:11px" fill="var(--muted)">Number</text>
    <g stroke="var(--grid)"><path d="M149.5 457v11M275.5 457v11M401.5 457v11M528.5 457v11M654.5 457v11M780.5 457v11M907.5 457v11M1033.5 457v11M1158.5 457v11"/></g>
    <g fill="var(--muted)" style="font-size:8px" text-anchor="middle">
      <text x="211" y="473">12/27/2020</text><text x="336" y="473">12/28/2020</text><text x="461" y="473">12/29/2020</text><text x="591" y="473">12/30/2020</text>
      <text x="717" y="473">12/31/2020</text><text x="843" y="473">01/01/2021</text><text x="965" y="473">01/02/2021</text><text x="1095" y="473">01/03/2021</text>
    </g>
    <rect x="569.5" y="246" width="3.5" height="211" rx="1.5" fill="var(--blue)"/>
  </svg>

  <div class="legend">
    <div class="legend-item" style="left:0;top:0"><span class="swatch" style="background:var(--blue)"></span>Scheduled Maintenance</div>
    <div class="legend-item" style="left:0;top:30px"><span class="swatch" style="background:var(--green)"></span>Completed Scheduled Maintenance</div>
    <div class="legend-item" style="left:0;top:60px"><span class="swatch" style="background:var(--orange)"></span>Future Scheduled Maintenance</div>
    <div class="legend-item" style="left:328px;top:0"><span class="swatch" style="background:var(--charcoal)"></span>Scheduled Work Orders</div>
    <div class="legend-item" style="left:328px;top:30px"><span class="swatch" style="background:var(--violet)"></span>Completed Work Orders</div>
    <div class="legend-item" style="left:612px;top:0"><span class="swatch" style="background:var(--pink)"></span>Property Inspections in Progress</div>
    <div class="legend-item" style="left:614px;top:30px"><span class="swatch" style="background:var(--yellow)"></span>Completed Property Inspections</div>
  </div>

  <div class="page-code">M1</div>
</div>
</body>
</html>
```